Business cards and Stationary for engineering design firm
Brell Systems Advisory
Creative Brief
Professional
Dana Morrow
President
42 N 3rd St Emmaus, PA 18062
Dana@BrellSysAdvisory.com
www.BrellSysAdvisory.com
We are looking for modern and professional looking business cards for an engineering firm that specializes in the electric utility industry. Subtle touches like abstract poles and wires on the business cards are welcomed. Use your imagination and have fun!
We are up for anything. Maybe just the company logo and the website address for the back.

```html
<!DOCTYPE html>
<html lang="en">
<head>
<meta charset="utf-8">
<title>Brell Systems Advisory – Stationery</title>
<link href="https://fonts.googleapis.com/css2?family=Montserrat:wght@500;600&family=Open+Sans:wght@400;600&display=swap" rel="stylesheet">
<style>
  :root{
    --navy:#1e3a66;
    --navy-deep:#182f55;
    --navy-soft:#2d4d80;
    --rule:#9aa3ad;
    --text:#4a4f57;
    --paper:#ffffff;
    --bg:#ffffff;
  }
  *{box-sizing:border-box;margin:0;padding:0}
  html,body{width:1200px;height:937px;overflow:hidden;background:var(--bg)}
  .stage{position:relative;width:1200px;height:937px}
  .sheet{position:absolute;background:var(--paper);overflow:hidden;box-shadow:0 2px 6px rgba(0,0,0,.22),0 0 1px rgba(0,0,0,.25)}
  .band{position:absolute;left:0;bottom:0;width:100%;display:block}

  .brand{display:flex;align-items:center;gap:.45em;font-family:'Montserrat',sans-serif;font-weight:600;color:var(--navy);letter-spacing:.02em;white-space:nowrap}
  .brand-square{display:block;width:.9em;height:.9em;background:var(--navy);flex:none}
  .tagline{font-family:'Open Sans',sans-serif;font-weight:400;color:var(--text);letter-spacing:.12em;text-transform:uppercase;white-space:nowrap}
  .small{font-family:'Open Sans',sans-serif;color:var(--text)}
  .centered{display:flex;flex-direction:column;align-items:center}

  /* Letterhead */
  .letterhead{left:182px;top:51px;width:395px;height:556px}
  .letterhead .head{position:absolute;top:40px;left:0;right:0}
  .letterhead .brand{font-size:12px}
  .letterhead .tagline{font-size:5px;margin-top:4px}
  .letter-body{position:absolute;top:112px;left:24px;width:330px;font-size:5.6px;line-height:8px}
  .letter-body p{margin-bottom:7px}
  .signature{width:40px;height:10px;background:linear-gradient(90deg,#2b2b2b,#888);opacity:.5;border-radius:5px;margin:4px 0 6px}
  .letterhead .contact{position:absolute;right:24px;bottom:18px;font-family:'Open Sans',sans-serif;font-size:5px;line-height:8px;color:#fff}

  /* Folder */
  .folder{left:633px;top:38px;width:417px;height:640px}
  .folder .head{position:absolute;top:262px;left:0;right:0}
  .folder .brand{font-size:22px}
  .folder .tagline{font-size:8.4px;margin-top:8px}
  .folder .web{position:absolute;right:30px;bottom:32px;font-family:'Montserrat',sans-serif;font-weight:600;font-size:9px;letter-spacing:.16em;color:#fff}

  /* Business cards */
  .card{width:251px}
  .card-front{left:40px;top:678px;height:84px}
  .card-front .brand{position:absolute;left:12px;top:16px;font-size:6px}
  .card-front .details{position:absolute;left:128px;top:12px;font-size:4.6px;line-height:6.4px}
  .card-front .details strong{color:var(--navy);font-weight:600}
  .card-back{left:40px;top:780px;height:88px}
  .card-back .head{position:absolute;top:36px;left:0;right:0}
  .card-back .brand{font-size:9px}

  /* Envelope front */
  .envelope{left:304px;top:673px;width:405px;height:200px}
  .envelope .brand{position:absolute;left:18px;top:24px;font-size:8px}
  .envelope .web{position:absolute;left:170px;top:128px;font-family:'Montserrat',sans-serif;font-weight:500;font-size:7px;letter-spacing:.14em;color:var(--text)}

  /* Envelope back */
  .envelope-back{left:739px;top:673px;width:425px;height:197px}
  .envelope-back svg{position:absolute;inset:0;width:100%;height:100%}
</style>
</head>
<body>
<svg width="0" height="0" style="position:absolute" aria-hidden="true">
  <defs>
    <linearGradient id="navyFill" x1="0" y1="0" x2="1" y2="1">
      <stop offset="0" stop-color="#2d4d80"/>
      <stop offset=".55" stop-color="#1e3a66"/>
      <stop offset="1" stop-color="#182f55"/>
    </linearGradient>
    <symbol id="slant" viewBox="0 0 400 130" preserveAspectRatio="none">
      <path d="M0,62 L400,14" fill="none" stroke="#9aa3ad" stroke-width="1.2"/>
      <path d="M0,78 L400,30 L400,130 L0,130Z" fill="url(#navyFill)"/>
    </symbol>
  </defs>
</svg>

<main class="stage">

  <section class="sheet letterhead" aria-label="Letterhead">
    <div class="head centered">
      <div class="brand"><span class="brand-square"></span>Brell Systems Advisory</div>
      <div class="tagline">Power Grid Engineering Services</div>
    </div>
    <div class="letter-body small">
      <p>July 8, 2019</p>
      <p>Alex Reed<br>Reed Holdings, Inc.<br>110 Main St, Allentown, PA</p>
      <p>Dear Alex,</p>
      <p>Thank you for meeting with our team last week. We are pleased to share our proposal for the substation upgrade and the new feeder line design. Our engineers have reviewed the site data and prepared a clear plan with milestones.</p>
      <p>The scope covers pole loading, joint use review and final drawings for permit.</p>
      <p>Please let us know if you have any questions. We look forward to working with you on this project and many more.</p>
      <p>Sincerely,</p>
      <div class="signature" role="img" aria-label="Handwritten signature"></div>
      <p>Dana Morrow<br>President</p>
    </div>
    <svg class="band" height="130" aria-hidden="true"><use href="#slant" width="100%" height="130"/></svg>
    <div class="contact">42 N 3rd St Emmaus, PA 18062<br>(610) 555-0142<br>Dana@BrellSysAdvisory.com<br>www.BrellSysAdvisory.com</div>
  </section>

  <section class="sheet folder" aria-label="Presentation folder">
    <div class="head centered">
      <div class="brand"><span class="brand-square"></span>Brell Systems Advisory</div>
      <div class="tagline">Power Grid Engineering Services</div>
    </div>
    <svg class="band" height="200" aria-hidden="true"><use href="#slant" width="100%" height="200"/></svg>
    <div class="web">www.BrellSysAdvisory.com</div>
  </section>

  <section class="sheet card card-front" aria-label="Business card front">
    <div class="brand"><span class="brand-square"></span>Brell Systems Advisory</div>
    <div class="details small">
      <strong>Dana Morrow</strong><br>President<br>42 N 3rd St Emmaus, PA 18062<br>(610) 555-0142<br>Dana@BrellSysAdvisory.com
    </div>
    <svg class="band" height="40" aria-hidden="true"><use href="#slant" width="100%" height="40"/></svg>
  </section>

  <section class="sheet card card-back" aria-label="Business card back">
    <div class="head centered">
      <div class="brand"><span class="brand-square"></span>Brell Systems Advisory</div>
    </div>
  </section>

  <section class="sheet envelope" aria-label="Envelope front">
    <div class="brand"><span class="brand-square"></span>Brell Systems Advisory</div>
    <div class="web">www.BrellSysAdvisory.com</div>
    <svg class="band" height="78" aria-hidden="true"><use href="#slant" width="100%" height="78"/></svg>
  </section>

  <section class="sheet envelope-back" aria-label="Envelope back">
    <svg viewBox="0 0 425 197" preserveAspectRatio="none" aria-hidden="true">
      <path d="M0,92 L425,92 L425,197 L0,197Z" fill="url(#navyFill)"/>
      <path d="M0,0 L212,74 L425,0" fill="none" stroke="#d3d7dc" stroke-width="1"/>
    </svg>
  </section>

</main>
</body>
</html>
```